zorvan lumet website design

An IT support and IT Security Company - just use dummy text for now for the design. Examples of sites we like the looks and feel of but need it more professional feel are like: www.kelbrovault.uk.com , www.pravok.co.uk, www.quenthardy.com/professional/, www.vur.com, www.melvish.com,

Best to message me if you have any questions

Target Market(s)

small to medium UK based companies that require IT support services

Industry/Entity Type

It Company

Contact Information for Business Card

use dummy name, telephone and email for now, will provide details later.

Logo Text

zorvan lumet (and then below the logo it should say "your IT, networks and security partner")

Coding

Coded - Design and coding required

Number of Pages Required

5+ page

Colors

Designer to choose colors to be used in the design.

Requirements
Must have
• must be professional, yet simple and clear that this is a serious IT support and IT security company.
Nice to have
• 1)The website homepage must have professional quality pictures of IT support or London city skyline or any picture that projects friendly business partners, professionalism and ready to serve.
• 2) Home page needs to include tabs for following pages 'Services' , 'About Us' , 'Contact Us' 'Home'
• 3) Website built customised using wordpress is ideal and easy for us to manage.
• more room for boxed options from homepage (with pic or image in background)
Should not have
• no checkout trolleys or payment options.

```html
<!DOCTYPE html>
<html lang="en">
<head>
<meta charset="utf-8">
<title>Zorvan Lumet – IT Support</title>
<link href="https://fonts.googleapis.com/css2?family=Oswald:wght@400;500&family=Roboto:wght@400;500;700&display=swap" rel="stylesheet">
<style>
:root{
  --orange:#f9b233;
  --teal-dark:#1a9478;
  --teal:#3bb594;
  --teal-light:#4fd4b4;
  --ink:#222;
  --muted:#666;
  --nav:#000;
  --nav-active:#6b6b6b;
  --footer:#2b2b2b;
  --footer-base:#191919;
  --panel:#f7f7f7;
  --line:#d6d6d6;
}
*{box-sizing:border-box;margin:0;padding:0}
html,body{width:1200px;height:2258px;overflow:hidden}
body{position:relative;background:#fff;font-family:"Roboto",sans-serif;color:var(--ink)}
.abs{position:absolute}

/* header */
.brand{left:200px;top:16px;font-family:"Roboto",sans-serif;font-weight:700;font-size:29px;color:var(--teal-dark);letter-spacing:.3px;line-height:36px;white-space:nowrap}
.brand-rule{left:200px;top:56px;width:168px;height:3px;background:var(--teal-dark)}
.contact-item{display:flex;gap:12px;align-items:flex-start;top:15px}
.contact-icon{width:40px;height:40px;background:var(--orange);display:flex;align-items:center;justify-content:center}
.contact-label{font-size:12px;font-weight:700;margin-top:4px}
.contact-value{font-size:11.5px;margin-top:5px;color:#333;white-space:nowrap}
.socials{left:882px;top:23px;display:flex;gap:7px}
.social{width:24px;height:24px;border-radius:50%;background:var(--teal)}

.nav{left:200px;top:71px;width:798px;height:36px;background:var(--nav);display:flex;color:#fff;font-size:13px;font-weight:500}
.nav-item{display:flex;align-items:center;gap:10px;padding-left:20px;border-right:2px solid #fff}
.nav-item.active{background:var(--nav-active)}
.nav-login{margin-left:auto;padding-right:16px;display:flex;align-items:center;gap:8px}

/* hero */
.hero{left:0;top:114px;width:1200px;height:449px;background:linear-gradient(100deg,#9a9a9a 0%,#4b4b4b 30%,#2a2a2a 60%,#3a3a3a 100%)}
.hero-title{right:202px;top:230px;font-family:"Oswald",sans-serif;font-size:50px;color:#fff;font-weight:500;white-space:nowrap}
.hero-text{right:202px;top:316px;text-align:right;color:#fff;font-size:15px;line-height:24px;font-weight:500;white-space:nowrap}
.btn-white{left:876px;top:399px;width:122px;height:41px;background:#fff;color:#222;font-size:13px;font-weight:700;display:flex;align-items:center;justify-content:center}
.arrow{top:319px;width:36px;height:39px;background:#fff;display:flex;align-items:center;justify-content:center}

/* intro */
.intro{left:200px;top:635px;width:798px;height:150px;border:2px solid var(--line)}
.intro-title{left:216px;top:670px;font-size:30px;line-height:36px;font-weight:500;font-family:"Oswald",sans-serif}
.intro-rule{left:445px;top:667px;width:3px;height:86px;background:var(--orange)}
.intro-text{left:470px;top:668px;width:505px;font-size:12px;line-height:20px;color:var(--muted)}

.section-title{font-family:"Oswald",sans-serif;font-size:29px;font-weight:500;display:flex;align-items:center;gap:12px;white-space:nowrap}
.section-title::after{content:"";width:3px;height:32px;background:var(--orange)}

/* services */
.card{top:917px;width:240px;height:193px;color:#fff;padding:18px 15px}
.card-head{display:flex;align-items:center;gap:10px;height:56px}
.card-title{font-size:14px;font-weight:700;line-height:18px}
.card-text{font-size:11.5px;line-height:20px;margin-top:14px;white-space:nowrap}
.card-link{font-size:11.5px;font-weight:700;margin-top:10px;display:flex;gap:8px;align-items:center}

/* about */
.about{left:200px;top:1174px;width:798px;height:286px;background:var(--panel);text-align:center}
.about-title{position:absolute;left:0;right:0;top:48px;display:flex;justify-content:center;align-items:center;gap:14px;font-family:"Oswald",sans-serif;font-size:29px;font-weight:500}
.about-title::before,.about-title::after{content:"";width:88px;height:2px;background:var(--orange)}
.about-text{position:absolute;left:50px;right:50px;top:104px;font-size:12px;line-height:20px;color:#444}
.btn-orange{background:var(--orange);color:#fff;font-size:12.5px;font-weight:700;display:flex;align-items:center;justify-content:center}

/* news */
.news{top:1591px;width:380px}
.news-date{position:absolute;left:0;top:0;width:45px;height:57px;background:var(--teal);color:#fff;text-align:center;font-size:14px;font-weight:700;line-height:25px}
.news-date hr{border:0;border-top:1.5px solid #fff;margin:1px 7px}
.news-title{position:absolute;left:59px;top:0;font-size:16.5px;line-height:22px;color:#333;font-weight:400;white-space:nowrap}
.news-text{position:absolute;left:0;top:80px;font-size:11.5px;line-height:20px;color:var(--muted);white-space:nowrap}
.news .btn-orange{position:absolute;left:0;top:179px;width:100px;height:37px}

/* footer */
.newsletter{left:0;top:1865px;width:1200px;height:125px;background:var(--footer);border-bottom:1px solid #444}
.newsletter-title{left:200px;top:1918px;color:var(--orange);font-family:"Oswald",sans-serif;font-size:27px;font-weight:500;display:flex;align-items:center;gap:14px}
.newsletter-title::after{content:"";width:3px;height:32px;background:var(--orange)}
.field{top:1917px;width:216px;height:41px;background:#fff;border:1px solid #999;font-size:11.5px;color:#888;padding:13px 14px}
.send{left:898px;top:1917px;width:100px;height:41px;gap:10px}
.footer{left:0;top:1990px;width:1200px;height:210px;background:var(--footer);color:#fff}
.f-col{top:2016px;font-size:12px;color:#fff}
.f-head{color:var(--orange);font-size:13.5px;margin-bottom:20px}
.f-col li{list-style:none;height:26px}
.f-contact{display:flex;gap:14px;margin-bottom:12px;line-height:21px}
.f-socials{display:flex;gap:8px;margin-bottom:14px}
.f-social{width:28px;height:28px;border-radius:50%;border:1.5px solid #fff}
.base{left:0;top:2200px;width:1200px;height:58px;background:var(--footer-base);color:#fff;font-size:12px;display:flex;align-items:center;justify-content:center}
</style>
</head>
<body>

<header>
  <div class="abs brand">ZORVAN LUMET</div>
  <div class="abs brand-rule"></div>

  <div class="abs contact-item" style="left:524px">
    <div class="contact-icon"><svg width="18" height="18" viewBox="0 0 24 24" fill="#fff"><path d="M6.6 10.8a15 15 0 0 0 6.6 6.6l2.2-2.2c.3-.3.7-.4 1-.2 1.1.4 2.3.6 3.6.6.6 0 1 .4 1 1V20c0 .6-.4 1-1 1A17 17 0 0 1 3 4c0-.6.4-1 1-1h3.5c.6 0 1 .4 1 1 0 1.3.2 2.5.6 3.6.1.3 0 .7-.2 1z"/></svg></div>
    <div><div class="contact-label">CALL :</div><div class="contact-value">+44 20 7946 0321</div></div>
  </div>
  <div class="abs contact-item" style="left:679px">
    <div class="contact-icon"><svg width="18" height="18" viewBox="0 0 24 24" fill="none" stroke="#fff" stroke-width="2"><path d="M3 10l9-6 9 6v10H3z"/><path d="M3 10l9 6 9-6"/></svg></div>
    <div><div class="contact-label">E-MAIL :</div><div class="contact-value">info@zorvanlumet.uk.com</div></div>
  </div>
  <div class="abs socials"><span class="social"></span><span class="social"></span><span class="social"></span><span class="social"></span></div>

  <nav class="abs nav">
    <div class="nav-item active" style="width:113px"><svg width="18" height="16" viewBox="0 0 24 20" fill="#fff"><path d="M12 1 1 11h3v8h6v-6h4v6h6v-8h3z"/></svg>Home</div>
    <div class="nav-item" style="width:132px"><svg width="18" height="18" viewBox="0 0 24 24" fill="none" stroke="#fff" stroke-width="2"><circle cx="12" cy="9" r="5"/><path d="M3 20h14l4-4"/></svg>Service</div>
    <div class="nav-item" style="width:150px"><svg width="16" height="16" viewBox="0 0 24 24" fill="#fff"><circle cx="12" cy="7" r="5"/><path d="M2 23c0-6 4-9 10-9s10 3 10 9z"/></svg>About Us</div>
    <div class="nav-item" style="border:0"><svg width="12" height="20" viewBox="0 0 14 24" fill="none" stroke="#fff" stroke-width="2"><rect x="1" y="1" width="12" height="22" rx="2"/></svg>Contact Us</div>
    <div class="nav-login"><svg width="14" height="16" viewBox="0 0 16 20" fill="#fff"><path d="M4 8V5a4 4 0 0 1 8 0v3h-2V5a2 2 0 0 0-4 0v3z"/><rect x="1" y="8" width="14" height="11" rx="1"/></svg>Login</div>
  </nav>
</header>

<section>
  <div class="abs hero" role="img" aria-label="Data centre aisle lined with server racks"></div>
  <h1 class="abs hero-title">Welcome to Zorvan Lumet</h1>
  <p class="abs hero-text">Lorem Ipsum is simply dummy text of the printing and typesetting industry.<br>Lorem Ipsum has been the industry's standard</p>
  <div class="abs btn-white">READ MORE</div>
  <div class="abs arrow" style="left:0"><svg width="16" height="10" viewBox="0 0 16 10" fill="none" stroke="#222" stroke-width="1.6"><path d="M15 5H1M5 1 1 5l4 4"/></svg></div>
  <div class="abs arrow" style="left:1164px"><svg width="16" height="10" viewBox="0 0 16 10" fill="none" stroke="#222" stroke-width="1.6"><path d="M1 5h14M11 1l4 4-4 4"/></svg></div>
</section>

<section>
  <div class="abs intro"></div>
  <h2 class="abs intro-title">IT Support for Your<br>Industry</h2>
  <div class="abs intro-rule"></div>
  <p class="abs intro-text">Lorem Ipsum is simply dummy text of the printing and typesetting industry. Lorem Ipsum has been the industry's standard dummy text ever since the 1500s, when an unknown printer took a galley of type and scrambled it to make a type specimen book. It has survived not only five centuries, but also the leap into electronic..</p>
</section>

<section>
  <h2 class="abs section-title" style="left:200px;top:846px">Our Services</h2>

  <div class="abs card" style="left:200px;background:var(--teal-dark)">
    <div class="card-head"><svg width="56" height="52" viewBox="0 0 56 52" fill="none" stroke="#fff" stroke-width="3"><path d="M8 22a20 20 0 0 1 36-10M48 30a20 20 0 0 1-36 10"/><rect x="20" y="16" width="8" height="22" fill="#fff"/><rect x="30" y="22" width="7" height="16" fill="#fff"/></svg><div class="card-title">Business Continuity</div></div>
    <p class="card-text">Lorem Ipsum is simply dummy text of<br>the printing and typesetting industry.<br>Lorem Ipsum dummy text....</p>
    <div class="card-link">READ MORE <svg width="12" height="9" viewBox="0 0 12 9" fill="none" stroke="#fff" stroke-width="1.8"><path d="M0 4.5h11M7 1l4 3.5L7 8"/></svg></div>
  </div>

  <div class="abs card" style="left:480px;background:var(--teal)">
    <div class="card-head"><svg width="54" height="54" viewBox="0 0 54 54" fill="none" stroke="#fff" stroke-width="3"><circle cx="27" cy="18" r="8"/><path d="M27 4v5M27 27v5M13 18h5M36 18h5M4 32l12 16h8M50 32 38 48h-8"/></svg><div class="card-title">IT Support &amp; Field<br>Services</div></div>
    <p class="card-text">Lorem Ipsum is simply dummy text of<br>the printing and typesetting industry.<br>Lorem Ipsum dummy text....</p>
    <div class="card-link">READ MORE <svg width="12" height="9" viewBox="0 0 12 9" fill="none" stroke="#fff" stroke-width="1.8"><path d="M0 4.5h11M7 1l4 3.5L7 8"/></svg></div>
  </div>

  <div class="abs card" style="left:760px;background:var(--teal-light)">
    <div class="card-head"><svg width="52" height="54" viewBox="0 0 52 54" fill="#fff"><circle cx="26" cy="20" r="11"/><path d="M4 54c0-12 10-18 22-18s22 6 22 18z"/><path d="M12 20a14 14 0 0 1 28 0" fill="none" stroke="#fff" stroke-width="3"/></svg><div class="card-title">Outsourced Service<br>Desk</div></div>
    <p class="card-text">Lorem Ipsum is simply dummy text of<br>the printing and typesetting industry.<br>Lorem Ipsum dummy text....</p>
    <div class="card-link">READ MORE <svg width="12" height="9" viewBox="0 0 12 9" fill="none" stroke="#fff" stroke-width="1.8"><path d="M0 4.5h11M7 1l4 3.5L7 8"/></svg></div>
  </div>
</section>

<section class="abs about">
  <h2 class="about-title">About Us</h2>
  <p class="about-text">Lorem Ipsum is simply dummy text of the printing and typesetting industry. Lorem Ipsum has been the industry's standard dummy text ever since the 1500s, when an unknown printer took a galley of type and scrambled it to make a type specimen book. It has survived not only five centuries, but also the leap into electronic..</p>
  <div class="abs btn-orange" style="left:337px;top:193px;width:124px;height:39px">READ MORE</div>
</section>

<section>
  <h2 class="abs section-title" style="left:200px;top:1517px">Our News</h2>
  <article class="abs news" style="left:200px">
    <div class="news-date">15<hr>Feb</div>
    <h3 class="news-title">Lorem Ipsum is simply dummy text of the<br>printing and typesetting industry.</h3>
    <p class="news-text">Lorem Ipsum is simply dummy text of the printing and typesettingdus-<br>try. Lorem Ipsum has been the industry's standard dummy text ever<br>since the 1500s, when an unknown printer took a galley of type and<br>scrambled it to make a type specimen book.</p>
    <div class="btn-orange">READ MORE</div>
  </article>
  <article class="abs news" style="left:620px">
    <div class="news-date">15<hr>Feb</div>
    <h3 class="news-title">Lorem Ipsum is simply dummy text of the<br>printing and typesetting industry.</h3>
    <p class="news-text">Lorem Ipsum is simply dummy text of the printing and typesettingdus-<br>try. Lorem Ipsum has been the industry's standard dummy text ever<br>since the 1500s, when an unknown printer took a galley of type and<br>scrambled it to make a type specimen book.</p>
    <div class="btn-orange">READ MORE</div>
  </article>
</section>

<footer>
  <div class="abs newsletter"></div>
  <h2 class="abs newsletter-title">OUR NEWSLETER</h2>
  <div class="abs field" style="left:443px">Name</div>
  <div class="abs field" style="left:670px">E-mail Address</div>
  <div class="abs btn-orange send">SEND <svg width="20" height="18" viewBox="0 0 20 18" fill="#fff"><path d="M0 8 20 0l-4 18-6-6 6-8-8 7z"/></svg></div>

  <div class="abs footer"></div>
  <div class="abs f-col" style="left:200px">
    <div class="f-head">COMPNAY</div>
    <ul><li>Home</li><li>Services</li><li>About Us</li><li>Contact Us</li></ul>
  </div>
  <div class="abs f-col" style="left:373px">
    <div class="f-head">QUICK LINKS</div>
    <ul><li>News</li><li>Account</li><li>Login</li><li>Help</li></ul>
  </div>
  <div class="abs f-col" style="left:548px">
    <div class="f-head">KEEP IN TOUCH</div>
    <div class="f-contact"><svg width="14" height="14" viewBox="0 0 24 24" fill="#fff" style="margin-top:3px"><path d="M6.6 10.8a15 15 0 0 0 6.6 6.6l2.2-2.2c.3-.3.7-.4 1-.2 1.1.4 2.3.6 3.6.6.6 0 1 .4 1 1V20c0 .6-.4 1-1 1A17 17 0 0 1 3 4c0-.6.4-1 1-1h3.5c.6 0 1 .4 1 1 0 1.3.2 2.5.6 3.6.1.3 0 .7-.2 1z"/></svg>+44 20 7946 0321</div>
    <div class="f-contact"><svg width="14" height="16" viewBox="0 0 14 20" fill="#fff" style="margin-top:3px"><path d="M7 0a7 7 0 0 0-7 7c0 5 7 13 7 13s7-8 7-13a7 7 0 0 0-7-7zm0 10a3 3 0 1 1 0-6 3 3 0 0 1 0 6z"/></svg>Lorem Ipsum is simply dummy text<br>of the printing</div>
    <div class="f-contact"><svg width="16" height="12" viewBox="0 0 16 12" fill="none" stroke="#fff" stroke-width="1.5" style="margin-top:5px"><rect x="1" y="1" width="14" height="10"/><path d="M1 1l7 6 7-6"/></svg>info@zorvanlumet.com</div>
  </div>
  <div class="abs f-col" style="left:862px">
    <div class="f-head">FOLLOW US</div>
    <div class="f-socials"><span class="f-social"></span><span class="f-social"></span><span class="f-social"></span><span class="f-social"></span></div>
    <ul><li>Privacy Policy</li><li>Terms and Condition</li></ul>
  </div>
  <div class="abs base">© Copyright 2018 zorvan lumet.&nbsp; All Rights Reserved.</div>
</footer>

</body>
</html>
```